Business Card Design

I am an Event and Wedding Planner in need of an eye catching business card featuring my logo (attached), my contact details, and my company tagline (Making every celebration glow with wonder...) I would like the tagline in font similar the logo's font.
Updates
I have just noticed that my logo has a misspelling so for the final design, I will be uploading a corrected logo as soon as I have it.
My apologies.
Reason: Waiting on a corrected logo...Lantern is misspelled and it should say Weddings not Wedding
The logo has been corrected so now Lantern is spelled correctly and it says Weddings instead of Wedding. Please use Edwardian Script ITC as the font for the tagline so it will match the logo. Thank you for your patience.
Target Market(s)
Engaged couples and people hosting milestone celebrations. 25-50 years old, predominately female
Industry/Entity Type
Business
Contact Information for Business Card
Rosalind Merrow, Event Manager / Owner, Mobile: 0491 868 254, Email: rosalind@velvetlanternco.com.au, www.velvetlanternco.com.au, Making every celebration glow with wonder...

```html
<!DOCTYPE html>
<html lang="en">
<head>
<meta charset="utf-8">
<title>Velvet Lantern – Business Card</title>
<link rel="stylesheet" href="https://fonts.googleapis.com/css2?family=Pinyon+Script&family=Great+Vibes&family=Cormorant+Garamond:ital,wght@0,500;1,600&display=swap">
<style>
  :root {
    --backdrop: #d9d9d9;
    --card: #f6fbfd;
    --ink: #111111;
    --accent: #c8282d;
    --band: #3f3f3f;
    --band-text: #e8e8e8;
  }
  * { box-sizing: border-box; margin: 0; padding: 0; }
  html, body { width: 1200px; height: 840px; overflow: hidden; }
  body {
    background: var(--backdrop);
    position: relative;
    color: var(--ink);
  }
  .card {
    position: absolute;
    width: 560px;
    height: 340px;
    background: var(--card);
    border-radius: 22px;
    overflow: hidden;
    box-shadow: 0 6px 18px rgba(0,0,0,.25);
  }
  .card--front { left: 50px; top: 70px; }
  .card--back { left: 590px; top: 430px; }

  /* Brand name (placeholder for the mark) */
  .brand {
    position: absolute;
    display: flex;
    align-items: center;
  }
  .brand__name {
    font-family: "Cormorant Garamond", serif;
    font-weight: 500;
    font-style: normal;
    color: var(--ink);
    white-space: nowrap;
    line-height: 1;
  }
  .brand__dot { background: var(--accent); border-radius: 50%; flex: none; }

  .card--front .brand {
    left: 0; right: 0; top: 0; bottom: 0;
    justify-content: center;
    gap: 16px;
  }
  .card--front .brand__name { font-size: 66px; }
  .card--front .brand__dot { width: 18px; height: 18px; }

  .card--back .brand { left: 30px; top: 112px; gap: 10px; }
  .card--back .brand__name { font-size: 36px; }
  .card--back .brand__dot { width: 10px; height: 10px; }

  /* Contact block */
  .person { position: absolute; right: 30px; top: 24px; text-align: right; }
  .person__name { font-family: "Great Vibes", cursive; font-size: 34px; line-height: 1.1; word-spacing: 6px; }
  .person__role {
    font-family: "Cormorant Garamond", serif;
    font-style: italic; font-weight: 600;
    font-size: 15px; letter-spacing: .5px;
  }
  .contact { position: absolute; right: 16px; top: 108px; list-style: none; }
  .contact__item { display: flex; justify-content: flex-end; align-items: center; gap: 10px; height: 27px; margin-bottom: 3px; }
  .contact__text { font-family: "Cormorant Garamond", serif; }
  .contact__text--phone { font-size: 21px; font-weight: 500; letter-spacing: 1px; }
  .contact__text--link { font-style: italic; font-weight: 600; font-size: 14px; }
  .contact__icon {
    width: 24px; height: 24px; border-radius: 4px;
    background: var(--accent); display: flex; align-items: center; justify-content: center;
    color: #fff; font-family: Arial, sans-serif; font-size: 14px; font-weight: bold;
  }

  .tagline-band {
    position: absolute; left: 0; right: 0; bottom: 0; height: 92px;
    background: var(--band);
    display: flex; align-items: center; justify-content: center;
  }
  .tagline {
    font-family: "Pinyon Script", cursive;
    font-size: 30px; color: var(--band-text); white-space: nowrap;
  }
</style>
</head>
<body>

<section class="card card--front" aria-label="Card front">
  <div class="brand">
    <span class="brand__name">Velvet Lantern</span>
    <span class="brand__dot"></span>
  </div>
</section>

<section class="card card--back" aria-label="Card back">
  <div class="brand">
    <span class="brand__name">Velvet Lantern</span>
    <span class="brand__dot"></span>
  </div>

  <div class="person">
    <p class="person__name">Rosalind Merrow</p>
    <p class="person__role">Event Manager / Owner</p>
  </div>

  <ul class="contact">
    <li class="contact__item">
      <span class="contact__text contact__text--phone">0491 868 254</span>
      <span class="contact__icon">
        <svg width="14" height="14" viewBox="0 0 24 24" aria-hidden="true"><path fill="#fff" d="M6.6 10.8a15.1 15.1 0 0 0 6.6 6.6l2.2-2.2c.3-.3.7-.4 1-.2 1.1.4 2.3.6 3.6.6.6 0 1 .4 1 1V20c0 .6-.4 1-1 1A17 17 0 0 1 3 4c0-.6.4-1 1-1h3.5c.6 0 1 .4 1 1 0 1.3.2 2.5.6 3.6.1.3 0 .7-.2 1z"/></svg>
      </span>
    </li>
    <li class="contact__item">
      <span class="contact__text contact__text--link">rosalind@velvetlanternco.com.au</span>
      <span class="contact__icon">@</span>
    </li>
    <li class="contact__item">
      <span class="contact__text contact__text--link">www.velvetlanternco.com.au</span>
      <span class="contact__icon">
        <svg width="14" height="14" viewBox="0 0 24 24" aria-hidden="true" fill="none" stroke="#fff" stroke-width="2"><circle cx="12" cy="12" r="9"/><ellipse cx="12" cy="12" rx="4" ry="9"/><path d="M3 12h18"/></svg>
      </span>
    </li>
  </ul>

  <div class="tagline-band">
    <p class="tagline">Making every celebration glow with wonder...</p>
  </div>
</section>

</body>
</html>
```